Redesign of business card for Cedar Ridge Mechanical

We are looking for a new design for our business cards for Cedar Ridge Mechanical. We are a plumbing & HVAC construction company, operating on the West Coast of Canada and USA. Logo attached.
Industry/Entity Type
Construction - Plumbing & HVAC
Contact Information for Business Card
Name, address, phone numbers, email, website address
Look and feel
Each slider illustrates characteristics of the customer's brand and the style your logo design should communicate.

```html
<!DOCTYPE html>
<html lang="en">
<head>
<meta charset="utf-8">
<title>Cedar Ridge Mechanical – Business Card</title>
<link href="https://fonts.googleapis.com/css2?family=Poppins:wght@400;700&display=swap" rel="stylesheet">
<style>
  :root {
    --stage: #232323;
    --card: #d6d7d6;
    --ink: #0c0c0c;
    --rule: #8a8b8a;
    --emboss: #c4c5c4;
  }
  * { margin: 0; padding: 0; box-sizing: border-box; }
  html, body { width: 1200px; height: 780px; overflow: hidden; }
  body {
    background: var(--stage);
    font-family: "Poppins", sans-serif;
    color: var(--ink);
    display: flex;
    align-items: center;
    justify-content: center;
    gap: 40px;
  }
  .card {
    position: relative;
    width: 540px;
    height: 310px;
    background: var(--card);
    border-radius: 22px;
    overflow: hidden;
  }
  .edge-bar {
    position: absolute;
    width: 12px;
    background: var(--ink);
  }
  .edge-bar--left { left: 0; top: 58px; height: 150px; }
  .edge-bar--right { right: 0; top: 178px; height: 110px; }

  .brand {
    position: absolute;
    left: 46px;
    top: 62px;
    width: 200px;
    display: flex;
    align-items: flex-start;
    gap: 12px;
  }
  .brand__square {
    flex: none;
    width: 22px;
    height: 22px;
    background: var(--ink);
    margin-top: 6px;
  }
  .brand__name {
    font-weight: 700;
    font-size: 24px;
    line-height: 1.15;
    text-transform: uppercase;
    letter-spacing: 0.5px;
  }
  .divider {
    position: absolute;
    left: 282px;
    top: 52px;
    width: 1px;
    height: 196px;
    background: var(--rule);
  }
  .address {
    position: absolute;
    left: 34px;
    bottom: 26px;
    font-size: 11.5px;
    font-weight: 400;
  }
  .person {
    position: absolute;
    left: 306px;
    top: 72px;
  }
  .person__name {
    font-size: 25px;
    line-height: 1.1;
    font-weight: 400;
  }
  .person__name strong { font-weight: 700; }
  .person__title {
    font-size: 12px;
    font-weight: 700;
    margin-top: 4px;
  }
  .contacts {
    list-style: none;
    margin-top: 14px;
    font-size: 12.5px;
  }
  .contacts li {
    display: flex;
    align-items: center;
    gap: 8px;
    margin-bottom: 4px;
  }
  .contacts svg { width: 11px; height: 11px; flex: none; }

  .card--back {
    display: flex;
    align-items: center;
    justify-content: center;
  }
  .back__mark {
    font-weight: 700;
    font-size: 38px;
    line-height: 1.1;
    text-transform: uppercase;
    text-align: center;
    color: var(--emboss);
    letter-spacing: 1px;
  }
</style>
</head>
<body>
  <section class="card card--front" aria-label="Business card front">
    <span class="edge-bar edge-bar--left"></span>
    <span class="edge-bar edge-bar--right"></span>

    <div class="brand">
      <span class="brand__square"></span>
      <span class="brand__name">Cedar Ridge Mechanical</span>
    </div>

    <span class="divider"></span>

    <p class="address">1840 Harbor Ln. Suite 300 Tacoma, WA 98402</p>

    <div class="person">
      <h1 class="person__name"><strong>Marta</strong> Kovacs</h1>
      <p class="person__title">Founder &amp; CEO</p>
      <ul class="contacts">
        <li>
          <svg viewBox="0 0 12 12" aria-hidden="true"><path d="M2.5 1h2l1 3-1.3 1a6 6 0 0 0 2.8 2.8l1-1.3 3 1v2a1 1 0 0 1-1 1A9.5 9.5 0 0 1 1.5 2a1 1 0 0 1 1-1z" fill="#0c0c0c"/></svg>
          (555) 214-0387
        </li>
        <li>
          <svg viewBox="0 0 12 12" aria-hidden="true"><circle cx="6" cy="6" r="5" fill="none" stroke="#0c0c0c" stroke-width="1.4"/><path d="M1 6h10M6 1c2 2.5 2 7.5 0 10M6 1c-2 2.5-2 7.5 0 10" fill="none" stroke="#0c0c0c" stroke-width="1"/></svg>
          info@cedarridgemech.com
        </li>
        <li>
          <svg viewBox="0 0 12 12" aria-hidden="true"><rect x="1" y="2.5" width="10" height="7" rx="1" fill="#0c0c0c"/><path d="M1.5 3l4.5 3.5L10.5 3" fill="none" stroke="#d6d7d6" stroke-width="1"/></svg>
          www.cedarridgemech.com
        </li>
      </ul>
    </div>
  </section>

  <section class="card card--back" aria-label="Business card back">
    <p class="back__mark">Cedar Ridge<br>Mechanical</p>
  </section>
</body>
</html>
```